VFX Company Business Card Design Project

The Kestrel Works is a decentralized Visual Effects Studio servicing the television and feature film industries.
Project Brief:
Take our logo that was previously designed on Pencil Harbor and make a double sided business card.
Requirements:
- Card MUST be double sided.
- Front of card MUST have the yellow part of our logo against the dark grey background.
- Back of card is completely up to the designer.
- Back of card must include the complete company logo.
Please follow these File Preparation guidelines:
http://printnook.ca/infopage?file=filetype_en&s=PrintNook_new&lang=en
Business

```html
<!DOCTYPE html>
<html lang="en">
<head>
<meta charset="utf-8">
<title>The Kestrel Works – Business Card</title>
<link rel="stylesheet" href="https://fonts.googleapis.com/css2?family=Jost:wght@300;400;500;600&family=Open+Sans:wght@400&display=swap">
<style>
  :root {
    --backdrop: #c9a27c;
    --card-dark: #2a2a2a;
    --card-light: #ffffff;
    --band-edge: #5f6b6e;
    --accent-yellow: #f9c623;
    --slate: #6b777a;
    --text-dark: #1e1e1e;
    --text-light: #ececec;
    --label: #111111;
  }
  * { box-sizing: border-box; margin: 0; padding: 0; }
  html, body { width: 1200px; height: 788px; overflow: hidden; }
  body {
    position: relative;
    background: var(--backdrop);
    font-family: "Jost", "Futura", sans-serif;
  }
  .side-label {
    position: absolute;
    font-family: "Open Sans", Arial, sans-serif;
    font-size: 21px;
    color: var(--label);
    transform: translateX(-50%);
    white-space: nowrap;
  }
  .label-back { left: 600px; top: 32px; }
  .label-front-1 { left: 327px; top: 404px; }
  .label-front-2 { left: 900px; top: 404px; }

  .card {
    position: absolute;
    width: 524px;
    height: 300px;
    border-radius: 22px;
    overflow: hidden;
    box-shadow: 3px 4px 10px rgba(0,0,0,0.35);
  }
  .card-back { left: 338px; top: 78px; background: var(--card-light); }
  .card-front-1 { left: 54px; top: 446px; background: var(--card-dark); }
  .card-front-2 { left: 622px; top: 446px; background: var(--card-dark); }

  .back-band { position: absolute; left: 0; top: 0; width: 524px; height: 170px; }
  .back-brand {
    position: absolute; left: 0; right: 0; top: 30px;
    text-align: center;
    font-size: 38px; font-weight: 500; letter-spacing: 1px;
    color: var(--slate);
  }
  .contact {
    position: absolute; left: 0; right: 0; top: 172px;
    text-align: center; color: var(--text-dark);
  }
  .contact-name { font-size: 21px; font-weight: 300; letter-spacing: 0.5px; }
  .contact-name small { font-size: 14px; font-weight: 400; }
  .contact-line { font-size: 14px; margin-top: 8px; }
  .contact-line b { font-weight: 600; font-style: italic; }

  .front-brand {
    position: absolute; left: 0; right: 0; top: 112px;
    text-align: center;
    font-size: 48px; font-weight: 600;
    color: var(--accent-yellow);
  }
  .front-lockup {
    position: absolute; left: 0; right: 0; top: 124px;
    display: flex; align-items: center; justify-content: center; gap: 16px;
  }
  .lockup-dot { width: 40px; height: 40px; border-radius: 50%; background: var(--accent-yellow); }
  .lockup-name { font-size: 36px; font-weight: 500; color: var(--slate); }
  .front-web {
    position: absolute; left: 0; right: 0; top: 256px;
    text-align: center;
    font-size: 20px; letter-spacing: 3px;
    color: var(--text-light);
  }
</style>
</head>
<body>
  <div class="side-label label-back">Back</div>
  <section class="card card-back">
    <svg class="back-band" viewBox="0 0 524 170" aria-hidden="true">
      <path d="M0 0 H524 V40 Q262 236 0 40 Z" fill="var(--band-edge)"/>
      <path d="M0 0 H524 V30 Q262 222 0 30 Z" fill="var(--card-dark)"/>
    </svg>
    <div class="back-brand">The Kestrel Works</div>
    <div class="contact">
      <p class="contact-name">Your Name, <small>Designation</small></p>
      <p class="contact-line"><b>phone</b> 123-456-7890 &nbsp;|&nbsp; <b>cell</b> 123-456-7890</p>
      <p class="contact-line"><b>email</b> info@website.com &nbsp;|&nbsp; <b>web</b> www.website.com</p>
      <p class="contact-line">0000#, Area Name, Street Name, State Name, Country code</p>
    </div>
  </section>

  <div class="side-label label-front-1">Front - 1</div>
  <section class="card card-front-1">
    <div class="front-brand">The Kestrel Works</div>
    <div class="front-web">www.website.com</div>
  </section>

  <div class="side-label label-front-2">Front - 2</div>
  <section class="card card-front-2">
    <div class="front-lockup">
      <span class="lockup-dot"></span>
      <span class="lockup-name">The Kestrel Works</span>
    </div>
    <div class="front-web">www.website.com</div>
  </section>
</body>
</html>
```